Lumbra Ember Oven Kitchen (restaurant)

Restaurant with a cool vibe.
We need a refresh of existing site. Appealing to a hip crowd of 25 or older age bracket (mid price to high small town). Constant changes food and cocktail menu. A vibing atmosphere with jazz funk hip music.
Must be able to scale for any device… phone/mobile device super important.
Instagram: @Lumbra.Bexwell
Website: lumbrabexwell.example

Target Market(s)

25-55 age group

Number of Pages Required

1 page

Font styles to use
Sans Serif

Requirements
Must have
• Simple to navigate. Simplicity is the key to all sophistication.

Links/Buttons
Menu
Gift Cards
Reservations
Take Out
Contact Us
Should not have
• Please, nothing generic looking… no cookie cutter look. Originality

```html
<!DOCTYPE html>
<html lang="en">
<head>
<meta charset="utf-8">
<title>Lumbra Ember Oven Kitchen</title>
<link href="https://fonts.googleapis.com/css2?family=Arvo:wght@400;700&family=Montserrat:ital,wght@0,400;0,500;0,600;0,700;0,800;1,400&family=Oswald:wght@400;500&display=swap" rel="stylesheet">
<style>
:root{
  --red:#d9181e;
  --red-dark:#a60f14;
  --ink:#1d1d1d;
  --char:#262626;
  --char-2:#2f2f2f;
  --paper:#ffffff;
  --mist:#f1f1f1;
  --grey:#6b6b6b;
  --soft:#bdbdbd;
  --gold:#f5d21c;
}
*{box-sizing:border-box;margin:0;padding:0}
html,body{width:1200px;height:4886px;overflow:hidden}
body{position:relative;background:var(--paper);font-family:"Montserrat",sans-serif;color:var(--ink)}
.section{position:absolute;left:0;width:1200px;overflow:hidden}
.fill{position:absolute}
.serif{font-family:"Arvo",serif;font-weight:700}
.rule{display:block;height:2px;background:currentColor;margin:10px auto 0}
.center{text-align:center}

/* header */
.site-header{top:0;height:82px;background:var(--paper);box-shadow:0 2px 6px rgba(0,0,0,.08);z-index:3}
.brand{position:absolute;left:100px;top:14px;text-align:center;width:170px}
.brand-name{font-weight:800;font-size:34px;letter-spacing:1px;line-height:36px}
.brand-sub{font-size:12px;font-weight:500;line-height:14px}
.nav{position:absolute;top:32px;left:384px;display:flex;gap:0}
.nav a{font-family:"Oswald",sans-serif;font-size:13px;color:var(--ink);text-decoration:none;text-transform:uppercase;margin-right:58px}
.nav a.active{color:var(--red)}

/* hero */
.hero{top:82px;height:620px}
.hero-photo{inset:0;background:linear-gradient(120deg,#5b3a2c 0%,#8a5240 35%,#a46650 55%,#4d3a33 80%,#2d2a2a 100%)}
.hero-disc{position:absolute;left:123px;top:96px;width:360px;height:360px;border-radius:50%;background:rgba(30,30,30,.72);color:#fff;text-align:center;padding-top:108px}
.hero-kicker{font-size:19px;letter-spacing:3px}
.hero-title{font-size:40px;line-height:46px;margin-top:6px}
.hero-disc .rule{width:40px;background:#fff;height:1px}
.btn-red{display:inline-block;background:var(--red);color:#fff;font-weight:700;font-size:13px;text-transform:uppercase;padding:10px 0;width:150px;text-align:center;box-shadow:4px 4px 0 -1px var(--paper),5px 5px 0 0 var(--red-dark)}
.hero-disc .btn-red{margin-top:28px;font-size:12px;width:148px;padding:8px 0}
.arrow{position:absolute;top:256px;width:40px;height:40px;border-radius:50%;background:#fff;display:flex;align-items:center;justify-content:center}

/* welcome */
.welcome{top:702px;height:649px}
.welcome-photo{left:0;top:0;width:608px;height:649px;background:radial-gradient(circle at 45% 45%,#d7a35b 0%,#8b4e36 35%,#4a2a2a 60%,#262626 100%)}
.text-block{position:absolute;text-align:center}
.heading{font-family:"Arvo",serif;font-weight:700;font-size:36px;text-transform:uppercase}
.body-copy{font-size:15px;line-height:29px;color:var(--grey);margin-top:30px}
.btn-dark{display:inline-block;background:var(--ink);color:#fff;font-weight:700;font-size:14px;text-transform:uppercase;width:180px;padding:12px 0;box-shadow:4px 4px 0 -1px var(--paper),5px 5px 0 0 var(--red)}

/* menu */
.menu{top:1351px;height:647px;background:radial-gradient(ellipse at 60% 40%,#3a3a3a 0%,#252525 60%,#1a1a1a 100%);color:#fff}
.menu-card{position:absolute;top:151px;width:240px;height:352px;display:flex;align-items:center;justify-content:center;text-align:center;font-family:"Arvo",serif;font-weight:700;font-size:20px;color:#fff;text-transform:uppercase;line-height:24px}
.menu-card.mono{background:linear-gradient(160deg,#8a8a8a,#4b4b4b 55%,#2f2f2f)}
.menu-card.featured{background:linear-gradient(160deg,#e36d60,#c9342c);}
.menu-card.featured::after{content:"";position:absolute;inset:10px;border:2px solid #fff}
.btn-outline{position:absolute;left:514px;top:541px;width:190px;height:44px;border:2px solid #fff;display:flex;align-items:center;justify-content:center;font-weight:700;font-size:15px}

/* reservation */
.reserve{top:1998px;height:548px;background:linear-gradient(120deg,#2c2c2c,#1e1e1e 70%,#333)}
.reserve-photo{left:0;top:0;width:610px;height:548px;background:linear-gradient(160deg,#6e4a36,#3d2c26 55%,#1f1b1b)}

/* takeout */
.takeout{top:2546px;height:516px;background:var(--paper)}
.takeout-photo{left:610px;top:0;width:590px;height:516px;background:radial-gradient(circle at 40% 55%,#d69a4b 0%,#a1583a 35%,#5f4c3a 65%,#3f3b38 100%)}

/* reviews */
.reviews{top:3062px;height:476px;background:var(--char);color:#fff}
.review{position:absolute;top:168px;width:300px;display:flex;gap:18px}
.avatar{flex:0 0 70px;height:70px;border-radius:50%;background:linear-gradient(160deg,#c9a58d,#6b4a3c);border:3px solid #fff}
.quote{font-size:11.5px;line-height:22px;color:#e8e8e8}
.quote b{font-family:"Arvo",serif;font-size:20px;margin-right:8px}
.reviewer{font-style:italic;font-size:13px;margin-top:12px}
.stars{margin-top:6px;color:var(--gold);font-size:18px;letter-spacing:3px}

/* gift cards */
.gifts{top:3538px;height:499px;background:linear-gradient(180deg,#ededed,#e0e0e0)}
.voucher{position:absolute;top:149px;width:486px;height:229px;background:var(--char);border-radius:50px 0 50px 0;overflow:hidden;color:#fff}
.voucher-photo{position:absolute;left:0;top:0;width:230px;height:229px}
.badge{position:absolute;left:190px;top:75px;width:78px;height:78px;border-radius:50%;background:#111;border:4px solid var(--red);text-align:center;padding-top:13px;font-weight:800;font-size:22px;line-height:22px}
.badge small{display:block;font-size:8px;font-weight:600;line-height:10px}
.voucher-text{position:absolute;left:270px;right:10px;top:48px;text-align:center}
.v-kicker{font-family:"Arvo",serif;font-size:16px}
.v-title{font-family:"Montserrat",sans-serif;font-weight:700;font-size:28px;line-height:30px}
.v-valid{font-size:9px;font-weight:700;margin-top:10px;border-top:1px solid #fff;padding-top:6px;display:inline-block}
.v-note{font-size:8.5px;line-height:14px;color:#ccc;margin-top:8px}
.dots{position:absolute;top:412px;left:568px;display:flex;gap:14px}
.dots i{display:block;width:26px;height:3px;background:#fff}
.dots i.on{background:var(--red)}

/* contact */
.contact{top:4037px;height:512px;background:var(--char);color:#fff}
.contact-photo{left:602px;top:0;width:598px;height:512px;background:linear-gradient(160deg,#8e8e8e,#5d5d5d 50%,#2e2e2e)}
.contact-item{position:absolute;left:152px;display:flex;align-items:center;gap:26px}
.contact-icon{width:60px;height:60px;border-radius:50%;background:#fff;display:flex;align-items:center;justify-content:center}
.contact-label{font-size:14px}
.contact-value{font-size:16px;font-weight:600;margin-top:2px}
.to-top{position:absolute;left:1061px;top:4528px;width:42px;height:42px;border-radius:50%;background:#555;display:flex;align-items:center;justify-content:center;z-index:2}

/* footer */
.footer{top:4549px;height:337px;background:radial-gradient(ellipse at 40% 30%,#2b2b2b,#141414 80%);color:#fff}
.foot-brand{position:absolute;left:128px;top:66px;width:190px;text-align:center}
.socials{position:absolute;left:154px;top:178px;display:flex;gap:10px}
.socials span{width:36px;height:36px;border-radius:50%;background:#fff;border:6px solid #555}
.copyright{position:absolute;left:128px;top:236px;width:190px;text-align:center;font-size:11px;line-height:17px;color:#cfcfcf}
.foot-col{position:absolute;top:71px}
.foot-col h4{font-size:14px;font-weight:700;text-transform:uppercase;padding-bottom:6px;border-bottom:2px solid #fff;display:inline-block}
.foot-col ul{list-style:none;margin-top:22px}
.foot-col li{font-size:11px;color:#cfcfcf;line-height:24px}
.foot-col li.icon{display:flex;align-items:center;gap:8px}
</style>
</head>
<body>

<header class="section site-header">
  <div class="brand"><div class="brand-name">LUMBRA</div><div class="brand-sub">Ember Oven Kitchen</div></div>
  <nav class="nav">
    <a class="active" href="#">Home</a><a href="#">About Us</a><a href="#">Menu</a><a href="#">Reservation</a><a href="#">Takeout</a><a href="#">Gift Cards</a><a href="#">Contact</a>
  </nav>
</header>

<section class="section hero">
  <div class="fill hero-photo" role="img" aria-label="Brick restaurant building on a street corner"></div>
  <div class="hero-disc">
    <div class="hero-kicker">WELCOME TO LUMBRA</div>
    <div class="hero-title serif">EMBER OVEN<br>KITCHEN</div>
    <span class="rule" style="width:40px"></span>
    <span class="btn-red">Reservation</span>
  </div>
  <div class="arrow" style="left:16px"><svg width="14" height="14" viewBox="0 0 14 14"><path d="M9 2 4 7l5 5" fill="none" stroke="#222" stroke-width="2"/></svg></div>
  <div class="arrow" style="left:1132px"><svg width="14" height="14" viewBox="0 0 14 14"><path d="M5 2l5 5-5 5" fill="none" stroke="#222" stroke-width="2"/></svg></div>
</section>

<section class="section welcome">
  <div class="fill welcome-photo" role="img" aria-label="Grilled tacos with red cabbage and sauce"></div>
  <div class="text-block" style="left:650px;width:475px;top:140px">
    <h2 class="heading">Welcome to Lumbra</h2>
    <span class="rule" style="width:150px;height:1px"></span>
    <p class="body-copy">Sed ut perspiciatis unde omnis iste natus error sit voluptatem accusantium doloremque<br>aperiam, eaque ipsa quae ab illo inventore veritatis et quasi architecto beatae vitae dicta sunt explicabo. Nemo enim ipsam voluptatem quia voluptas sit asper-natur aut odit aut fugit, sed quia</p>
    <div style="margin-top:50px;margin-left:-10px"><span class="btn-dark">Learn More</span></div>
  </div>
</section>

<section class="section menu">
  <div class="text-block" style="left:0;width:1200px;top:46px">
    <h2 class="heading" style="font-size:36px">Our Menu</h2>
    <span class="rule" style="width:282px;height:1px"></span>
  </div>
  <div class="menu-card mono" style="left:88px" role="img" aria-label="Burger photo">Special Burger</div>
  <div class="menu-card mono" style="left:347px" role="img" aria-label="Sandwiches photo">Sandwiches</div>
  <div class="menu-card featured" style="left:607px" role="img" aria-label="Ember oven pizza photo">Ember Oven<br>Pizza</div>
  <div class="menu-card mono" style="left:866px" role="img" aria-label="Fired pizza photo">Fired Pizza</div>
  <div class="btn-outline">VIEW MENU</div>
</section>

<section class="section reserve">
  <div class="fill reserve-photo" role="img" aria-label="Restaurant team posing by the oven"></div>
  <div class="text-block" style="left:650px;width:470px;top:146px;color:#fff">
    <div style="font-family:'Arvo',serif;font-size:30px">BOOK YOUR</div>
    <h2 class="heading" style="font-size:42px;margin-top:6px">Reservation</h2>
    <p class="body-copy" style="color:#eee;margin-top:14px">Sed ut perspiciatis unde omnis iste natus error sit voluptatem accusantium doloremque</p>
    <div style="margin-top:30px"><span class="btn-red" style="width:190px">Reservation</span></div>
  </div>
</section>

<section class="section takeout">
  <div class="text-block" style="left:90px;width:460px;top:136px">
    <h2 class="heading">Take Out</h2>
    <span class="rule" style="width:228px;height:1px"></span>
    <p class="body-copy" style="margin-top:24px">Sed ut perspiciatis unde omnis iste natus error sit voluptatem accusantium doloremque<br>aperiam, eaque ipsa quae ab illo inventore veritatis et quasi architecto beatae vitae dicta sunt explicabo</p>
    <div style="margin-top:36px"><span class="btn-red" style="width:180px">Book Now</span></div>
  </div>
  <div class="fill takeout-photo" role="img" aria-label="Chicken tacos with avocado, onion and lime"></div>
</section>

<section class="section reviews">
  <div class="text-block" style="left:0;width:1200px;top:60px">
    <div style="font-size:18px">REVIEWS</div>
    <h2 class="heading" style="font-size:32px;margin-top:2px">What People Says</h2>
  </div>
  <div class="review" style="left:140px"><div class="avatar" role="img" aria-label="Guest portrait"></div><div><p class="quote"><b>“</b>At vero eos et accusamus et iustodio dignissimos ducimus qui blanditiipraesnt ium volutm deleniti atque crupquos</p><div class="reviewer">Mara Quill</div><div class="stars">★★★★☆</div></div></div>
  <div class="review" style="left:452px"><div class="avatar" role="img" aria-label="Guest portrait"></div><div><p class="quote"><b>“</b>At vero eos et accusamus et iustodio dignissimos ducimus qui blanditiipraesnt ium volutm deleniti atque crupquos</p><div class="reviewer">Mara Quill</div><div class="stars">★★★★☆</div></div></div>
  <div class="review" style="left:768px"><div class="avatar" role="img" aria-label="Guest portrait"></div><div><p class="quote"><b>“</b>At vero eos et accusamus et iustodio dignissimos ducimus qui blanditiipraesnt ium volutm deleniti atque crupquos</p><div class="reviewer">Mara Quill</div><div class="stars">★★★★☆</div></div></div>
  <svg style="position:absolute;left:565px;top:388px" width="70" height="34" viewBox="0 0 70 34"><circle cx="16" cy="17" r="14" fill="none" stroke="#fff" stroke-width="1.5"/><path d="M19 11l-6 6 6 6" fill="none" stroke="#fff" stroke-width="1.5"/><circle cx="52" cy="17" r="14" fill="none" stroke="#fff" stroke-width="1.5"/><path d="M49 11l6 6-6 6" fill="none" stroke="#fff" stroke-width="1.5"/></svg>
</section>

<section class="section gifts">
  <div class="text-block" style="left:0;width:1170px;top:68px">
    <h2 class="heading" style="font-size:32px">Gift Cards</h2>
    <span class="rule" style="width:110px;height:1px;color:#555"></span>
  </div>
  <div class="voucher" style="left:110px">
    <div class="voucher-photo" role="img" aria-label="Bowls of dips and sauces" style="background:radial-gradient(circle at 50% 50%,#c88a3a,#6f6a2a 45%,#2c2a22)"></div>
    <div class="badge">35%<small>DISCOUNT</small></div>
    <div class="voucher-text"><div class="v-kicker">MAIN MEAL</div><div class="v-title">VOUCHER</div><div class="v-valid">VALID 20 AUG 2021</div><p class="v-note">Sed ut perspiciatis unde omnis iste natus error sit avoluptatem accusantium</p></div>
  </div>
  <div class="voucher" style="left:610px">
    <div class="voucher-photo" role="img" aria-label="Fired pizza slices" style="background:radial-gradient(circle at 45% 50%,#e0573a,#a83a24 45%,#3a2a22)"></div>
    <div class="badge" style="background:#111;border-color:#f5a31c">25%<small>DISCOUNT</small></div>
    <div class="voucher-text"><div class="v-kicker" style="color:var(--red)">FIRED PIZZA</div><div class="v-title">VOUCHER</div><div class="v-valid">VALID 20 AUG 2021</div><p class="v-note">Sed ut perspiciatis unde omnis iste natus error sit avoluptatem accusantium</p></div>
  </div>
  <div class="dots"><i></i><i class="on"></i></div>
</section>

<section class="section contact">
  <div style="position:absolute;left:152px;top:104px">
    <div style="font-size:18px;letter-spacing:2px">CONTACT US</div>
    <h2 class="heading" style="font-size:36px;margin-top:4px">Get in Touch</h2>
  </div>
  <div class="contact-item" style="top:196px"><div class="contact-icon"><svg width="24" height="24" viewBox="0 0 24 24"><path d="M6 3l3 4-2 2c1 3 4 6 7 7l2-2 4 3-2 3C10 20 4 14 3 5z" fill="none" stroke="#d9181e" stroke-width="1.6"/></svg></div><div><div class="contact-label">Phone Number</div><div class="contact-value">555-014-2287</div></div></div>
  <div class="contact-item" style="top:271px"><div class="contact-icon"><svg width="24" height="24" viewBox="0 0 24 24"><path d="M3 11 21 3l-8 18-2-8z" fill="#d9181e"/></svg></div><div><div class="contact-label">Email enquiry</div><div class="contact-value">enquiry@lumbra.example</div></div></div>
  <div class="contact-item" style="top:346px"><div class="contact-icon"><svg width="24" height="24" viewBox="0 0 24 24"><path d="M12 2a7 7 0 0 0-7 7c0 5 7 13 7 13s7-8 7-13a7 7 0 0 0-7-7z" fill="#d9181e"/><circle cx="12" cy="9" r="2.5" fill="#fff"/></svg></div><div><div class="contact-label">Location</div><div class="contact-value">1820 Alder Row, Bexwell</div></div></div>
  <div class="fill contact-photo" role="img" aria-label="Black and white photo of the restaurant building"></div>
</section>

<div class="to-top"><svg width="16" height="16" viewBox="0 0 16 16"><path d="M8 13V3M3 8l5-5 5 5" fill="none" stroke="#fff" stroke-width="1.5"/></svg></div>

<footer class="section footer">
  <div class="foot-brand"><div class="brand-name" style="font-size:38px">LUMBRA</div><div class="brand-sub" style="font-size:13px">Ember Oven Kitchen</div></div>
  <div class="socials" aria-label="Social links"><span></span><span></span><span></span></div>
  <p class="copyright">Copyright © 2021 Lumbra<br>All Right Reserved</p>
  <div class="foot-col" style="left:392px"><h4>Navigation</h4><ul><li>Our Menu</li><li>Gift Cards</li><li>Reservation</li><li>Takeout</li><li>Contact Us</li></ul></div>
  <div class="foot-col" style="left:584px"><h4>Working Hours</h4><ul><li>Thursday, July 1st - &nbsp;Open</li><li>Friday, July 2nd - &nbsp;Open</li><li>Saturday, July 3rd - &nbsp;Open</li><li>Sunday, July 4th - &nbsp;Closed</li></ul></div>
  <div class="foot-col" style="left:833px"><h4>Contact Us</h4><ul>
    <li style="font-weight:700;color:#fff">LUMBRA</li>
    <li class="icon"><svg width="12" height="12" viewBox="0 0 24 24"><path d="M12 2a7 7 0 0 0-7 7c0 5 7 13 7 13s7-8 7-13a7 7 0 0 0-7-7z" fill="#d9181e"/></svg>48 Quarry Lane | Bexwell, ON | K0L 2P4</li>
    <li class="icon"><svg width="12" height="12" viewBox="0 0 24 24"><path d="M6 3l3 4-2 2c1 3 4 6 7 7l2-2 4 3-2 3C10 20 4 14 3 5z" fill="#d9181e"/></svg>Phone: 555-019-0473</li>
    <li class="icon"><svg width="12" height="12" viewBox="0 0 24 24"><rect x="3" y="6" width="18" height="12" fill="none" stroke="#d9181e" stroke-width="2"/><path d="M3 6l9 7 9-7" fill="none" stroke="#d9181e" stroke-width="2"/></svg>Email: hello@lumbrabexwell.example</li>
  </ul></div>
</footer>

</body>
</html>
```